Business Card - high end, modern health care

Hey designers!

We need a double sided business card for the boutique, cutting edge physical therapy rehabilitation centre in Sydney's Northern Beaches.

With the most qualified physios in the area The Harbourview Motion Clinic does what other physiotherapy practices do not, we take our time with our patients giving them longer appointments, better physios and therefor faster results!

We guarantee that the service people receive at THMC will be unparalleled.

Hence we need a business card to reflect our modern, boutique, high end service. The final design needs to reflect that we are in a class of our own yet with the feel of beachside retreat.

Below I have attached our logo in both blue on white and white on blue. The exact colour is;
and the font that we have used in our logo is Tex Gyre Aventador.

I like the idea of the blue as the main colour as it is more eye catching and our signage onto the main road will be in this blue and in the interest of consistency across marketing the blue needs to be a part of the design. However I would appreciate a few designs onto a wooden background as this is a visual theme within the fitout of the practice.

The design needs to be of standard size (91x55mm).

Target Market(s)

We target people who have an end outcome in mind and those who have had poor experiences with other providers and ensure that everyone gets the care that they deserve with a premium service that is tailored to the individuals circumstances. As a premium service, the target market is highly educated, business and tech savvy with the additional target market of elderly people who have self funded their retirement and see value in paying for the best ongoing rehabilitation to maintain independence.

Industry/Entity Type

Physical Therapy

Contact Information for Business Card

Name, designation( Titled Musculoskeletal Physiotherapist... there will also be those in the company that have multiple designations ie 5 or 6 words long), phone number, email, facebook, instagram, address

Font styles to use
Sans Serif

Colors

Designer to choose colors to be used in the design.

Requirements
Must have
• Front - The logo as large as possible, blue or wooden theme, and all of the important details.
• Back - A blank space/lines on which to write appointment times (no "Appointment, date, time" etc.)
Nice to have
• facebook url
• logos for facebook and instagram
• Mini logos for the phone and email?

```html
<!DOCTYPE html>
<html lang="en">
<head>
<meta charset="utf-8">
<title>The Harbourview Motion Clinic – Business Card</title>
<link rel="stylesheet" href="https://fonts.googleapis.com/css2?family=Lato:wght@400;700&display=swap">
<style>
  :root {
    --brand-blue: #0b56a7;
    --card-white: #ffffff;
    --ink-dark: #222222;
    --ink-muted: #7a7a7a;
    --page-bg: #ececec;
  }
  * { margin: 0; padding: 0; box-sizing: border-box; }
  html, body {
    width: 1200px;
    height: 900px;
    overflow: hidden;
    background: var(--page-bg);
    font-family: "Lato", Arial, sans-serif;
  }
  .business-card {
    position: absolute;
    left: 120px;
    top: 152px;
    width: 960px;
    height: 595px;
    background: var(--card-white);
    overflow: hidden;
    box-shadow: 0 10px 30px rgba(0, 0, 0, 0.15);
  }
  .panel-background {
    position: absolute;
    inset: 0;
    width: 100%;
    height: 100%;
  }
  .panel-fill { fill: var(--brand-blue); }
  .appointment-strip { fill: var(--card-white); }

  .person {
    position: absolute;
    right: 54px;
    top: 70px;
    text-align: right;
  }
  .person-name {
    color: var(--brand-blue);
    font-size: 32px;
    font-weight: 400;
    letter-spacing: 0.5px;
    line-height: 34px;
  }
  .person-title {
    color: var(--ink-dark);
    font-size: 24px;
    line-height: 30px;
  }

  .contact-line {
    position: absolute;
    left: 53px;
    display: flex;
    align-items: center;
    gap: 8px;
    color: var(--card-white);
    font-size: 25px;
    line-height: 30px;
  }
  .contact-phone { top: 208px; }
  .contact-email { top: 245px; }
  .social-page { top: 482px; }
  .social-handle { top: 517px; }

  .contact-icon {
    width: 30px;
    height: 30px;
    flex: none;
  }
  .social-dot {
    width: 28px;
    height: 28px;
    border-radius: 50%;
    background: var(--card-white);
    flex: none;
    margin-right: 2px;
  }

  .appointment-field {
    position: absolute;
    left: 53px;
    color: var(--ink-muted);
    font-size: 22px;
    font-weight: 700;
    display: flex;
    align-items: flex-end;
    line-height: 26px;
  }
  .appointment-field .write-line {
    display: inline-block;
    width: 130px;
    border-bottom: 2px solid var(--ink-muted);
    margin-left: 2px;
    margin-bottom: 4px;
  }
  .field-date { top: 335px; }
  .field-time { top: 394px; }

  .brand-mark {
    position: absolute;
    left: 683px;
    top: 265px;
    width: 206px;
    height: 206px;
    border-radius: 50%;
    background: var(--brand-blue);
  }
  .brand-name {
    position: absolute;
    left: 636px;
    top: 484px;
    width: 300px;
    text-align: center;
    color: var(--brand-blue);
    font-size: 21px;
    font-weight: 700;
    letter-spacing: 0.6px;
    line-height: 25px;
  }
</style>
</head>
<body>
  <main class="business-card">
    <svg class="panel-background" viewBox="0 0 960 595" aria-hidden="true">
      <path class="panel-fill" d="M0 0 L520 0 Q430 300 560 595 L0 595 Z"/>
      <rect class="appointment-strip" x="0" y="315" width="540" height="140"/>
    </svg>

    <header class="person">
      <div class="person-name">DANIEL CARTER</div>
      <div class="person-title">Managing Director</div>
    </header>

    <div class="contact-line contact-phone">
      <svg class="contact-icon" viewBox="0 0 30 30" aria-hidden="true">
        <circle cx="15" cy="15" r="13" fill="none" stroke="#fff" stroke-width="2"/>
        <path d="M10.5 8.5 l2.5 -0.5 l1.5 3.5 l-1.8 1.3 c0.8 1.8 2 3 3.8 3.8 l1.3 -1.8 l3.5 1.5 l-0.5 2.5 c-6 0.5 -10.8 -4.3 -10.3 -10.3 z" fill="#fff"/>
      </svg>
      <span>402 718 3390</span>
    </div>
    <div class="contact-line contact-email">
      <svg class="contact-icon" viewBox="0 0 30 30" aria-hidden="true">
        <circle cx="15" cy="15" r="13" fill="#fff"/>
        <rect x="8" y="10" width="14" height="10" rx="1" fill="#0b56a7"/>
        <path d="M8.5 10.5 L15 15.5 L21.5 10.5" fill="none" stroke="#fff" stroke-width="1.5"/>
      </svg>
      <span>hello@harbourviewmotion.com</span>
    </div>

    <div class="appointment-field field-date">DATE<span class="write-line"></span></div>
    <div class="appointment-field field-time">TIME<span class="write-line"></span></div>

    <div class="contact-line social-page">
      <span class="social-dot"></span>
      <span>/harbourviewmotionclinic</span>
    </div>
    <div class="contact-line social-handle">
      <span class="social-dot"></span>
      <span>@harbourviewmotionclinic</span>
    </div>

    <div class="brand-mark"></div>
    <div class="brand-name">THE HARBOURVIEW<br>MOTION CLINIC</div>
  </main>
</body>
</html>
```